Awsome new website

We are a Fencing Contracting company in Melbourne Australia. We supply and install Timer and Steel boundary fences as well as Pool fencing (e.g. glass, tubular steel). We also manufacture and install swing and sliding gates.

We want a new website that is a modern business website.
We are targeting domestic and business clients.
The design should compliment our logo and company name.
The website needs to be easy to update.

Some specifics we want.
Menu - Main menu at top of page and smaller footer menu (to add different menu items)
Slider - Main page to have a slider on it that's easy for us to add and remove slides.
Call to action - all pages to have a "call to action" logo or icon that attracts attention (see file "call_to_action.pdf)
Instant quote - we have a online quote page we need a distinctive logo or icon to redirect to this page.
Main page to have a product /Service guide (see file "website_idea.jpg")
Main page to have widgets or quick link to
o why choose us
o Brochures
o Gallery

Have a Gallery page formatted with different category galleries. e.g. Timber, Glass, Feature
Maintain the current link to our staff page with password, (link in footer menu)

Hopefully that covers everything.
Our current website is www.tallgumfencing.com.au to have a look at the current site.
regards Doug

• Turn off blogging as we don’t want 100’s of comments from spammers to delete

We would like to implement the Portalio plugin (see "http://portalio-plug.net/" ), but this can be done after the new Theme has been implemented.

```html
<!DOCTYPE html>
<html lang="en">
<head>
<meta charset="utf-8">
<title>Tall Gum Fencing</title>
<link href="https://fonts.googleapis.com/css2?family=Open+Sans:ital,wght@0,400;0,600;0,700;1,400&display=swap" rel="stylesheet">
<style>
:root{
  --brand-red:#8b1219;
  --brand-red-dark:#6e0d12;
  --title-red:#8a1a1f;
  --link-red:#9a2228;
  --nav-top:#6c727a;
  --nav-bottom:#4f545b;
  --band-grey:#efefef;
  --panel-grey:#f2f2f2;
  --panel-border:#dcdcdc;
  --body-text:#333333;
  --footer-bg:#58585a;
  --white:#ffffff;
}
*{margin:0;padding:0;box-sizing:border-box}
html,body{width:944px;height:1200px;overflow:hidden}
body{position:relative;font-family:"Open Sans",sans-serif;color:var(--body-text);background:var(--white)}
.abs{position:absolute}

.hero{left:0;top:0;width:944px;height:454px;background:linear-gradient(180deg,var(--brand-red) 0%,var(--brand-red) 38%,#a2464b 62%,#c3a7a9 85%,#d4d0d0 100%)}
.brand{left:142px;top:36px;display:flex;align-items:center;gap:6px;color:var(--white)}
.brand-mark{width:14px;height:14px;background:var(--white)}
.brand-name{font-size:17px;font-weight:700;line-height:1}
.brand-tagline{left:142px;top:66px;font-size:6px;font-weight:700;color:var(--white);letter-spacing:.2px}
.follow{left:645px;top:58px;display:flex;align-items:center;gap:6px;color:var(--white);font-size:7.5px}
.follow span.dot{width:18px;height:18px;border-radius:50%;background:var(--white);display:inline-block;margin-left:-1.5px}
.follow-label{margin-right:4px}

.main-nav{left:142px;top:91px;width:662px;height:34px;border-radius:3px;background:linear-gradient(180deg,var(--nav-top),var(--nav-bottom));box-shadow:0 1px 2px rgba(0,0,0,.3)}
.main-nav a{position:absolute;top:9px;color:var(--white);font-size:12px;text-decoration:none;transform:translateX(-50%);white-space:nowrap}

.slider{left:142px;top:134px;width:661px;height:256px;background:linear-gradient(120deg,#6a4a25 0%,#c6993f 30%,#e4cf9e 55%,#b58c4f 80%,#7a6040 100%);box-shadow:0 24px 30px -10px rgba(0,0,0,.55)}
.slide-caption{left:494px;top:327px;color:var(--white);font-size:17.5px;font-weight:600;line-height:22px;text-shadow:1px 1px 2px rgba(0,0,0,.6)}
.slider-dots{left:446px;top:425px;display:flex;gap:6px}
.slider-dots i{width:8px;height:8px;border-radius:50%;background:var(--brand-red);display:block}
.slider-dots i.active{background:#e6e6e6;box-shadow:inset 0 0 0 1px #bbb}

.newsletter{left:0;top:454px;width:944px;height:83px;background:var(--band-grey)}
.newsletter-title{left:160px;top:28px;font-size:19px;color:#333}
.newsletter-title small{font-size:12.5px;margin-left:6px;color:#444}
.btn-red{display:flex;align-items:center;justify-content:center;color:var(--white);background:linear-gradient(180deg,#9b1c22,var(--brand-red-dark));border-radius:2px;box-shadow:0 0 0 1px #c55 inset;text-decoration:none}
.subscribe{left:604px;top:21px;width:164px;height:39px;font-size:12.5px;font-weight:600}

.section-title{color:var(--title-red);font-size:16px;font-weight:400}
.body-copy{font-size:7.5px;line-height:13.6px;color:#222}

.welcome{left:141px;top:552px;width:414px}
.welcome .body-copy{margin-top:8px;font-size:7.2px;letter-spacing:-.1px}
.welcome .body-copy p+p{margin-top:13.6px}

.services{left:140px;top:708px;width:419px;height:250px;background:var(--panel-grey);border:1px solid var(--panel-border)}
.services .section-title{position:absolute;left:19px;top:12px}
.services .rule{position:absolute;left:19px;top:40px;width:383px;height:1px;background:#d6d6d6}
.seal{position:absolute;left:14px;top:55px}
.service-list{position:absolute;list-style:none;font-size:7.5px;color:var(--link-red)}
.service-list li{height:18.3px;display:flex;align-items:center;gap:6px}
.address-bar{position:absolute;left:14px;top:194px;width:391px;height:39px;background:linear-gradient(180deg,#eceef0,#dfe2e6);border:1px solid #c9cdd2;font-size:8px;line-height:37px;padding-left:12px;color:#555}
.address-bar span{color:var(--link-red)}

.news{left:140px;top:979px;width:420px}
.news-arrows{left:542px;top:984px;font-size:10px;color:#aaa;letter-spacing:3px}
.news-item{position:absolute;top:1016px;width:187px}
.news-item h3{font-size:10px;font-weight:400;color:#222;padding-bottom:6px;border-bottom:2px solid #d8d8d8}
.news-item .body-copy{margin-top:10px}
.news-item .posted{margin-top:4px;font-size:7.5px;font-style:italic;color:var(--link-red)}

.quote-tile{left:587px;top:561px;width:216px;height:97px;background:linear-gradient(135deg,#3b4048 0%,#8a9098 45%,#d6cfc6 75%,#b98b6a 100%)}
.quote-tile .label{position:absolute;left:0;bottom:0;width:100%;height:24px;background:rgba(40,40,40,.6);color:var(--white);font-size:11px;padding:4px 12px}

.why{left:586px;top:674px;width:217px;height:186px;background:var(--panel-grey);border:1px solid var(--panel-border)}
.why .section-title{position:absolute;left:21px;top:10px}
.why .body-copy{position:absolute;left:23px;top:43px;width:176px;font-size:6.6px;line-height:12.2px;word-break:break-all}
.read-more{position:absolute;left:27px;top:137px;width:99px;height:30px;font-size:8.5px}

.brochure{left:586px;top:876px;width:217px;height:58px;background:linear-gradient(180deg,#6c727a,#4f545b);border:1px solid #464a50}
.brochure .doc-icon{position:absolute;left:15px;top:10px;width:38px;height:38px;background:#e9e9e9;border-radius:3px}
.brochure strong{position:absolute;left:67px;top:11px;color:var(--white);font-size:12.5px;font-weight:600}
.brochure em{position:absolute;left:68px;top:35px;color:#e5e5e5;font-size:7px}

.gallery-title{left:586px;top:945px;font-size:12.5px;font-weight:600;color:var(--title-red)}
.gallery-arrows{left:784px;top:949px;font-size:9px;color:#aaa;letter-spacing:3px}
.gallery-frame{left:587px;top:974px;width:216px;height:138px;border:1px solid #ddd;padding:5px;background:var(--white)}
.gallery-photo{width:100%;height:100%;background:linear-gradient(120deg,#3a2a22 0%,#b8aa98 35%,#ece8e2 55%,#6e4a30 80%,#2e2a28 100%)}

.footer{left:0;top:1146px;width:944px;height:54px;background:var(--footer-bg);color:var(--white)}
.footer-nav{position:absolute;left:141px;top:19px;font-size:7px;display:flex;align-items:center}
.footer-nav a{color:var(--white);text-decoration:none}
.footer-nav .sep{margin:0 19px}
.copyright{position:absolute;left:627px;top:19px;font-size:7px}
</style>
</head>
<body>

<header class="hero abs">
  <div class="brand abs"><span class="brand-mark"></span><span class="brand-name">Tall Gum Fencing</span></div>
  <div class="brand-tagline abs">WHEN QUALITY COUNTS, COUNT ON US</div>
  <div class="follow abs"><span class="follow-label">Follow us :</span><span class="dot"></span><span class="dot"></span><span class="dot"></span><span class="dot"></span><span class="dot"></span></div>

  <nav class="main-nav abs">
    <a style="left:52px">Home</a>
    <a style="left:145px">Steelguard</a>
    <a style="left:260px">Instant Quote</a>
    <a style="left:360px">Gallery</a>
    <a style="left:476px">Products &amp; Services</a>
    <a style="left:606px">Contact</a>
  </nav>

  <div class="slider abs" role="img" aria-label="Slide photo of a modern warm-toned kitchen interior"></div>
  <div class="slide-caption abs">Tall Gum Fencing<br>When quality counts,Count on &nbsp;us</div>
  <div class="slider-dots abs"><i></i><i></i><i class="active"></i><i></i><i></i></div>
</header>

<section class="newsletter abs">
  <div class="newsletter-title abs">Newsletter Signup<small>Get our recent updates through your Email Id</small></div>
  <a class="btn-red subscribe abs">Join now Subscribe</a>
</section>

<section class="welcome abs">
  <h2 class="section-title">Welcome to Tall Gum Fencing</h2>
  <div class="body-copy">
    <p>Thank you for visiting us at Tall Gum Fencing, my name is Doug and I am the Manager.<br>I built my first fence when I was in my early twenties and have been building fences ever since. Over the last few years we have spent the time looking for fantastic fencing contractors to join our team. Because we only accept the best we have built our business to be one of Victoria's largest fencing contractors.</p>
    <p>At Tall Gum Fencing, we believe in quality above all. The first fence we constructed was over 25 years ago and the number one thing we have learnt is that to do the job right the first time is the best insurance against costly rework.</p>
  </div>
</section>

<section class="services abs">
  <h2 class="section-title">New Services List</h2>
  <div class="rule"></div>
  <svg class="seal" width="130" height="130" viewBox="0 0 130 130" role="img" aria-label="Quality badge">
    <circle cx="65" cy="65" r="64" fill="#d9dadc"/>
    <circle cx="65" cy="65" r="56" fill="#f4f4f4"/>
    <circle cx="65" cy="65" r="50" fill="none" stroke="#c8222b" stroke-width="4"/>
    <circle cx="65" cy="65" r="32" fill="none" stroke="#c8222b" stroke-width="2"/>
  </svg>
  <ul class="service-list" style="left:158px;top:70px">
    <li><svg width="7" height="6" viewBox="0 0 7 6"><path d="M0 6 Q1 2 5 2 V0 L7 3 L5 6 V4 Q2 4 0 6Z" fill="#555"/></svg>Bathroom Remodeling</li>
    <li><svg width="7" height="6" viewBox="0 0 7 6"><path d="M0 6 Q1 2 5 2 V0 L7 3 L5 6 V4 Q2 4 0 6Z" fill="#555"/></svg>Attic &amp; Garage Finishing</li>
    <li><svg width="7" height="6" viewBox="0 0 7 6"><path d="M0 6 Q1 2 5 2 V0 L7 3 L5 6 V4 Q2 4 0 6Z" fill="#555"/></svg>Carpentry</li>
    <li><svg width="7" height="6" viewBox="0 0 7 6"><path d="M0 6 Q1 2 5 2 V0 L7 3 L5 6 V4 Q2 4 0 6Z" fill="#555"/></svg>Tile &amp; Flooring</li>
    <li><svg width="7" height="6" viewBox="0 0 7 6"><path d="M0 6 Q1 2 5 2 V0 L7 3 L5 6 V4 Q2 4 0 6Z" fill="#555"/></svg>Decks</li>
  </ul>
  <ul class="service-list" style="left:280px;top:70px">
    <li><svg width="7" height="6" viewBox="0 0 7 6"><path d="M0 6 Q1 2 5 2 V0 L7 3 L5 6 V4 Q2 4 0 6Z" fill="#555"/></svg>General Home Maintenance</li>
    <li><svg width="7" height="6" viewBox="0 0 7 6"><path d="M0 6 Q1 2 5 2 V0 L7 3 L5 6 V4 Q2 4 0 6Z" fill="#555"/></svg>Painting 7 Wall Treatments</li>
    <li><svg width="7" height="6" viewBox="0 0 7 6"><path d="M0 6 Q1 2 5 2 V0 L7 3 L5 6 V4 Q2 4 0 6Z" fill="#555"/></svg>Drywall Install</li>
    <li><svg width="7" height="6" viewBox="0 0 7 6"><path d="M0 6 Q1 2 5 2 V0 L7 3 L5 6 V4 Q2 4 0 6Z" fill="#555"/></svg>Electrical</li>
    <li><svg width="7" height="6" viewBox="0 0 7 6"><path d="M0 6 Q1 2 5 2 V0 L7 3 L5 6 V4 Q2 4 0 6Z" fill="#555"/></svg>Fences</li>
  </ul>
  <div class="address-bar">412 Wattle Lane,Ringwood, VIC 3134. <span>Telephone: +61 3 9555 0142, Fax: +61 3 9555 0178</span></div>
</section>

<section class="news abs">
  <h2 class="section-title">Latest News</h2>
</section>
<div class="news-arrows abs">‹ ›</div>
<article class="news-item" style="left:145px">
  <h3>A new Steelguard</h3>
  <p class="body-copy">Fence is an investment that will increase the value of your home, please download our Steelguard™ Brochure.</p>
  <p class="posted">Posted on 27 Oct 2013</p>
</article>
<article class="news-item" style="left:367px">
  <h3>A new Steelguard</h3>
  <p class="body-copy">Fence is an investment that will increase the value of your home, please download our Steelguard™ Brochure.</p>
  <p class="posted">Posted on 27 Oct 2013</p>
</article>

<a class="quote-tile abs" role="img" aria-label="Photo of hands typing on a laptop keyboard"><span class="label">Online Quote &gt;&gt;</span></a>

<aside class="why abs">
  <h2 class="section-title">Why choose us</h2>
  <p class="body-copy">We offer a 12 month workmanshhttp://tallgumfencing.com.au/images/site-theme/aboutus.jpgip warranty on our fences and will clean the site for free of any debris from the fence construction upon completion of the job. We can offer this workmanship warranty because of our work practices, these include</p>
  <a class="btn-red read-more">Read more info</a>
</aside>

<a class="brochure abs"><span class="doc-icon"></span><strong>Brochure download</strong><em>Click here for download our Brouchure</em></a>

<h2 class="gallery-title abs">Photo Gallery</h2>
<div class="gallery-arrows abs">‹ ›</div>
<div class="gallery-frame abs"><div class="gallery-photo" role="img" aria-label="Gallery photo of a modern kitchen with timber cabinets"></div></div>

<footer class="footer abs">
  <nav class="footer-nav">
    <a>Home Page</a><span class="sep">|</span>
    <a>Steelguard</a><span class="sep">|</span>
    <a>Instant Quote</a><span class="sep">|</span>
    <a>Gallery</a><span class="sep">|</span>
    <a>Products &amp; Services</a><span class="sep">|</span>
    <a>Contact</a>
  </nav>
  <div class="copyright">Copyrights 2013 © Tall Gum Fencing. All rights reserved.</div>
</footer>

</body>
</html>
```